Real Estate Team Business Card

We need a business card designed for our real estate team called "Maplecrest Realty Group". We would like to receive a final format that would allow us to edit the contact information for new employees as they are added to our team. The difficult part of the design is that we will need to have two logos on the card - both our team name logo for "Maplecrest Realty Group" and our company logo for "Summitpoint Real Estate". Most emphasis should be given to the team logo - maybe double the size of our company logo. (we just have to have the company logo somewhere on the card for legal purposes) The design should somehow illustrate we work in real estate, but still use the beehive/bee concept as a lot of our marketing will involve "bee" sayings. We would also like to use the tagline: "see why the whole street is talking". We also need to use the "fair housing" logo and "realtor" logos. These can both be small like the company logo.
Target Market(s)
Real Estate
Industry/Entity Type
Real Estate Agent
Contact Information for Business Card
Name: Darren Pulaski Title: Realtor Phone: 801-372-5518 Email: darren@maplecrestrealtrygroup.com Website: www.maplecrestrealtygroup.com Facebook: fb/me/maplecrestrealtygroup Twitter: @MaplecrestRltyGrp
Colors
Designer to choose colors to be used in the design.
Requirements
Must have
- Contact information. Maplecrest Realty Group Logo. Summitpoint Real Estate Logo. Realtor logo. Fair Housing Logo. Tagline: "see why the whole street is talking".
Nice to have
- It would be nice to illustrate that we work in real estate. It would also be nice to somehow incorporate bees or play off of our beehive logo. We will do a lot of marking using sayings like "let us bee the solution" or "real estate meant to bee" etc.

```html
<!DOCTYPE html>
<html lang="en">
<head>
<meta charset="utf-8">
<title>Maplecrest Realty Group – Business Card</title>
<link href="https://fonts.googleapis.com/css2?family=Josefin+Sans:wght@400;600&family=Open+Sans:wght@400;600&display=swap" rel="stylesheet">
<style>
  :root {
    --bg: #e6e6e8;
    --card: #ffffff;
    --ink: #1a1a1a;
    --muted: #555555;
    --honey: #f5c400;
    --honey-soft: #ffd633;
    --partner-blue: #1e5fae;
    --badge: #9a9a9a;
  }
  * { margin: 0; padding: 0; box-sizing: border-box; }
  html, body { width: 1200px; height: 1000px; overflow: hidden; }
  body {
    background: var(--bg);
    font-family: "Open Sans", Arial, sans-serif;
    color: var(--ink);
    position: relative;
  }
  .card {
    position: absolute;
    left: 240px;
    width: 720px;
    height: 411px;
    background: var(--card);
    box-shadow: 0 6px 18px rgba(0,0,0,.15);
    overflow: hidden;
  }
  .card--back { top: 60px; }
  .card--front { top: 520px; }

  /* back */
  .badges { position: absolute; top: 22px; right: 24px; display: flex; gap: 12px; }
  .badge { width: 30px; height: 30px; background: var(--badge); }
  .back-brand {
    position: absolute; left: 0; right: 0; top: 110px;
    display: flex; flex-direction: column; align-items: center;
  }
  .brand-mark { width: 42px; height: 42px; background: var(--honey); margin-bottom: 18px; }
  .brand-name {
    font-family: "Josefin Sans", Arial, sans-serif;
    font-weight: 600; color: var(--ink); text-align: center; line-height: 1;
  }
  .brand-name__main { display: block; font-size: 50px; letter-spacing: 6px; }
  .brand-name__sub { display: block; font-size: 16px; letter-spacing: 6px; margin-top: 8px; }
  .tagline {
    position: absolute; left: 0; right: 0; top: 318px;
    text-align: center; font-size: 19px; color: var(--muted);
  }

  /* front */
  .roof-band { position: absolute; left: 0; top: 0; width: 720px; height: 411px; }
  .agent { position: absolute; left: 30px; top: 28px; }
  .agent__name { color: var(--honey); font-size: 22px; font-weight: 600; letter-spacing: .5px; }
  .agent__company { color: var(--partner-blue); font-size: 15px; font-weight: 600; margin-top: 4px; }
  .contact {
    position: absolute; right: 26px; top: 40px;
    list-style: none; text-align: right; font-size: 17px; line-height: 25px;
  }
  .contact li { display: flex; justify-content: flex-end; align-items: center; gap: 10px; }
  .contact svg { width: 16px; height: 16px; flex: none; }
  .front-brand { position: absolute; left: 130px; top: 282px; width: 330px; }
  .front-brand .brand-name__main { font-size: 42px; letter-spacing: 5px; }
  .front-brand .brand-name__sub { font-size: 15px; }
</style>
</head>
<body>

<section class="card card--back" aria-label="Card back">
  <div class="badges" aria-hidden="true">
    <span class="badge"></span>
    <span class="badge"></span>
  </div>
  <div class="back-brand">
    <span class="brand-mark"></span>
    <p class="brand-name">
      <span class="brand-name__main">MAPLECREST</span>
      <span class="brand-name__sub">REALTY GROUP</span>
    </p>
  </div>
  <p class="tagline">see why the whole street is talking</p>
</section>

<section class="card card--front" aria-label="Card front">
  <svg class="roof-band" viewBox="0 0 720 411" role="img" aria-label="Wide yellow roof-line band">
    <defs>
      <linearGradient id="bandFill" x1="0" y1="0" x2="1" y2="1">
        <stop offset="0" stop-color="var(--honey-soft)"/>
        <stop offset="1" stop-color="var(--honey)"/>
      </linearGradient>
    </defs>
    <polygon points="0,200 330,40 640,411 560,411 330,110 0,270" fill="url(#bandFill)"/>
  </svg>
  <div class="agent">
    <p class="agent__name">DARREN PULASKI</p>
    <p class="agent__company">Summitpoint Real Estate</p>
  </div>
  <ul class="contact">
    <li>darren@maplecrestrealtrygroup.com
      <svg viewBox="0 0 16 16"><rect x="1" y="3" width="14" height="10" fill="var(--honey)"/><path d="M1 3l7 6 7-6" stroke="#fff" stroke-width="1.5" fill="none"/></svg></li>
    <li>801-372-5518
      <svg viewBox="0 0 16 16"><path d="M4 2l3 3-2 2a8 8 0 0 0 4 4l2-2 3 3-2 2C6 14 2 10 2 4z" fill="var(--honey)"/></svg></li>
    <li>www.maplecrestrealtygroup.com
      <svg viewBox="0 0 16 16"><circle cx="8" cy="8" r="7" fill="var(--honey)"/><path d="M1 8h14M8 1c-3 4-3 10 0 14M8 1c3 4 3 10 0 14" stroke="#fff" stroke-width="1" fill="none"/></svg></li>
    <li>fb/me/maplecrestrealtygroup
      <svg viewBox="0 0 16 16"><circle cx="8" cy="8" r="7" fill="var(--honey)"/></svg></li>
    <li>@MaplecrestRltyGrp
      <svg viewBox="0 0 16 16"><circle cx="8" cy="8" r="7" fill="var(--honey)"/></svg></li>
  </ul>
  <div class="front-brand">
    <p class="brand-name">
      <span class="brand-name__main">MAPLECREST</span>
      <span class="brand-name__sub">REALTY GROUP</span>
    </p>
  </div>
</section>

</body>
</html>
```